website design for M&T Electric

A portfolio website for a high end commercial and residential electrical contracting company. The current site mandtelectric.example does not represent the current direction but the images in the gallery give you an idea of the work we do. Current logo will be uploaded shortly but is black text on white background.
Target Market(s)
General Contractors, Residential Home Owners, clients intersted in Velmora home automation.
Industry/Entity Type
Electrician
Coding
Coded - Design and coding required
Number of Pages Required
2 page
Font styles to use
Sans Serif
Colors
Designer to choose colors to be used in the design.
Requirements
Must have
- Portfolio section highlighting different service areas and products (Velmora Housepilot, etc)

```html
<!DOCTYPE html>
<html lang="en">
<head>
<meta charset="utf-8">
<title>M&amp;T Electric</title>
<link href="https://fonts.googleapis.com/css2?family=Old+Standard+TT:wght@400;700&family=Open+Sans:wght@400;600&family=Oswald:wght@300;400&display=swap" rel="stylesheet">
<style>
:root{
  --black:#0b0b0b;
  --ink:#1c1c1c;
  --body:#555;
  --muted:#8a8a8a;
  --white:#fff;
  --light:#f0f0f0;
  --serif:"Old Standard TT", Georgia, serif;
  --sans:"Open Sans", Arial, sans-serif;
  --cond:"Oswald", "Arial Narrow", sans-serif;
}
*{box-sizing:border-box;margin:0;padding:0}
html,body{width:1200px;height:3939px;overflow:hidden}
body{font-family:var(--sans);color:var(--ink);background:var(--white);position:relative}
.abs{position:absolute}
.btn{display:inline-block;background:var(--black);color:var(--white);font-family:var(--serif);font-size:22px;letter-spacing:1px;text-transform:uppercase;padding:16px 34px;border-radius:34px;box-shadow:0 6px 12px rgba(0,0,0,.35);white-space:nowrap}
.btn.ghost{background:transparent;border:2px solid var(--white);box-shadow:none;padding:14px 30px}
.topbar{top:0;left:0;width:1200px;height:48px;background:var(--black);color:var(--white);font-size:17px}
.social{left:78px;top:8px;display:flex;gap:8px}
.social span{width:30px;height:30px;border-radius:50%;background:var(--white)}
.contact-top{right:80px;top:12px;display:flex;gap:34px;align-items:center}
.contact-top span{display:flex;align-items:center;gap:10px}
.nav{top:48px;left:0;width:1200px;height:88px;background:var(--white)}
.wordmark{font-family:var(--sans);font-weight:400;white-space:nowrap}
.logo{left:78px;top:18px;font-size:44px;color:var(--ink)}
.menu{right:78px;top:32px;display:flex;gap:28px;font-size:17px;text-transform:uppercase;align-items:center}
.hero{top:136px;left:0;width:1200px;height:574px;background:linear-gradient(100deg,#3a3630 0%,#2c2a27 40%,#5b5a56 70%,#2b2a28 100%)}
.keypad{left:78px;top:192px;width:200px;height:246px;background:linear-gradient(#5a4a34,#2a2118);border-radius:6px}
.hero h1{left:386px;top:210px;font-family:var(--cond);font-weight:300;font-size:60px;color:var(--white);white-space:nowrap}
.hero p{left:386px;top:300px;width:780px;font-size:15px;line-height:26px;color:var(--white)}
.hero .btn{left:390px;top:384px}
.arrow{top:250px}
.section-title{font-family:var(--serif);font-weight:400;font-size:52px;color:var(--ink);text-align:center;width:1200px;left:0}
.lead{left:140px;width:920px;text-align:center;font-size:14px;line-height:30px;color:var(--body)}
.svc-band{top:1242px;left:0;width:1200px;height:347px;background:linear-gradient(90deg,#141414,#2a2a2a 50%,#141414)}
.svc{top:1129px;width:334px}
.svc .ph{width:334px;height:218px}
.svc h3{font-family:var(--serif);font-weight:400;font-size:28px;color:var(--white);text-align:center;margin-top:26px}
.svc p{font-size:14px;line-height:29px;color:#d8d8d8;text-align:center;margin-top:8px;padding:0 10px}
.about h2{font-family:var(--serif);font-weight:400;font-size:48px}
.gal-band{top:2109px;left:0;width:1200px;height:748px;background:linear-gradient(90deg,#161616,#3a3530 50%,#161616)}
.gal-head{top:2035px;left:79px;width:1042px;height:171px;background:var(--light)}
.tabs{top:2150px;left:0;width:1200px;display:flex;justify-content:center;gap:18px;font-size:19px}
.tabs span{padding:6px 20px;border-radius:20px}
.tabs .on{background:var(--black);color:var(--white)}
.tile{width:322px;height:216px}
.tile .cap{position:absolute;left:0;top:130px;width:210px;height:56px;background:rgba(255,255,255,.22);font-family:var(--serif);font-size:26px;color:var(--white);padding:10px 26px;white-space:nowrap}
.prod{top:3009px;width:266px;height:352px;text-align:center}
.prod .ph{margin:24px auto 0;height:150px}
.prod h4{font-family:var(--serif);font-weight:400;font-size:22px;line-height:30px;margin-top:30px}
.prod p{font-size:14px;line-height:29px;color:#999;margin-top:12px;padding:0 18px}
.prod.active{background:#e8e8e8}
.prod.active p{color:var(--body)}
.news{top:3427px;left:0;width:1200px;height:165px;background:var(--light)}
.news h2{left:112px;top:52px;font-family:var(--serif);font-weight:400;font-size:46px}
.news .field{left:358px;top:58px;width:510px;height:58px;background:var(--white);border:1px solid #bbb;font-size:15px;color:#777;padding:18px 20px}
.news .btn{left:882px;top:56px}
.footer{top:3592px;left:0;width:1200px;height:347px;background:var(--black);color:var(--white)}
.footer .flogo{left:84px;top:86px;font-size:34px}
.fsocial{left:118px;top:160px;display:flex;gap:12px}
.fsocial span{width:46px;height:46px;border-radius:50%;border:2px solid #888;background:#2a2a2a}
.fcol{top:40px;font-size:14px;line-height:30px;color:#ccc}
.fcol h5{font-family:var(--serif);font-weight:400;font-size:17px;color:var(--white);letter-spacing:1px;margin-bottom:12px}
.crow{display:flex;gap:14px;align-items:flex-start}
.copy{top:3890px;left:0;width:1200px;text-align:center;font-size:14px;color:#aaa;border-top:1px solid #333;padding-top:16px}
</style>
</head>
<body>

<div class="abs topbar">
  <div class="abs social"><span></span><span></span><span></span></div>
  <div class="abs contact-top">
    <span><svg width="18" height="18" viewBox="0 0 24 24"><path fill="#fff" d="M6.6 10.8a15 15 0 0 0 6.6 6.6l2.2-2.2c.3-.3.7-.4 1-.2 1.1.4 2.3.6 3.6.6.6 0 1 .4 1 1V20c0 .6-.4 1-1 1A17 17 0 0 1 3 4c0-.6.4-1 1-1h3.5c.6 0 1 .4 1 1 0 1.3.2 2.5.6 3.6.1.3 0 .7-.2 1z"/></svg>(555) 014-2290</span>
    <span><svg width="18" height="14" viewBox="0 0 24 18"><rect x="1" y="1" width="22" height="16" fill="none" stroke="#fff" stroke-width="2"/><path d="M1 1l11 9 11-9" fill="none" stroke="#fff" stroke-width="2"/></svg>office@mandtelectric.example</span>
  </div>
</div>

<header class="abs nav">
  <div class="abs logo wordmark">M&amp;T Electric</div>
  <nav class="abs menu">
    <span>Home</span><span>About</span><span>Speciality Services</span><span>Product</span><span>Gallery</span><span>Contact</span>
    <svg width="22" height="22" viewBox="0 0 24 24"><circle cx="10" cy="10" r="7" fill="none" stroke="#111" stroke-width="3"/><path d="M15 15l7 7" stroke="#111" stroke-width="3"/></svg>
  </nav>
</header>

<section class="abs hero" role="img" aria-label="Dim modern living room interior with large windows">
  <div class="abs keypad" role="img" aria-label="Wall-mounted lighting control keypad"></div>
  <h1 class="abs">M&amp;T Electric In Your Home</h1>
  <p class="abs">We're Velmora Housepilot and Velmora Motorized Shades certified, as well as an authorized Brightvolt generator dealer. We've served the Alder Valley and Upper Plains area for over 18 years.</p>
  <span class="abs btn">Contact Us</span>
  <svg class="abs arrow" style="left:28px" width="20" height="70" viewBox="0 0 20 70"><path d="M18 2L2 35l16 33" fill="none" stroke="#ddd" stroke-width="2"/></svg>
  <svg class="abs arrow" style="right:28px" width="20" height="70" viewBox="0 0 20 70"><path d="M2 2l16 33L2 68" fill="none" stroke="#ddd" stroke-width="2"/></svg>
</section>

<h2 class="abs section-title" style="top:760px">Welcome To M&amp;T Electric</h2>
<p class="abs lead" style="top:838px">M&amp;T Electric is a full service electrical contracting shop. We offer commercial, residential, light industrial, and agricultural services. We're Velmora Housepilot and Velmora Motorized Shades certified, as well as an authorized Brightvolt generator dealer. We've served the Alder Valley and Upper Plains area for over 18 years.</p>
<p class="abs lead" style="top:936px">M&amp;T Electric is a full service electrical contracting shop. We offer commercial, residential, light industrial, and agricultural services. We're Velmora Housepilot and Velmora Motorized Shades certified, as well as an authorized Brightvolt generator dealer.</p>
<span class="abs btn" style="left:502px;top:1010px">Know More</span>

<div class="abs svc-band"></div>
<div class="abs svc" style="left:79px">
  <div class="ph" role="img" aria-label="Modern commercial building exterior" style="background:linear-gradient(#9fb6d6,#c9a7a0 60%,#8a8a8a)"></div>
  <h3>Commercial</h3>
  <p>M&amp;T Electric is a full service electrical contr- acting shop. We offer commercial, residential, light industrial, and agricultural services. We're Velmora Housepilot and Velmora</p>
</div>
<div class="abs svc" style="left:433px">
  <div class="ph" role="img" aria-label="Stone residential building at dusk" style="background:linear-gradient(#b9c3d4,#8b7b6a 55%,#5e5a55)"></div>
  <h3>Residential</h3>
  <p>M&amp;T Electric is a full service electrical contr- acting shop. We offer commercial, residential, light industrial, and agricultural services. We're Velmora Housepilot and Velmora</p>
</div>
<div class="abs svc" style="left:788px">
  <div class="ph" role="img" aria-label="Home with landscape lighting at night" style="background:linear-gradient(#1d2a45,#3a3146 55%,#a06a3a)"></div>
  <h3>Landscape</h3>
  <p>M&amp;T Electric is a full service electrical contr- acting shop. We offer commercial, residential, light industrial, and agricultural services. We're Velmora Housepilot and Velmora</p>
</div>

<section class="about">
  <h2 class="abs" style="left:79px;top:1642px">About M&amp;T Electric</h2>
  <p class="abs" style="left:79px;top:1720px;width:540px;font-size:14px;line-height:30px;color:var(--body)">M&amp;T Electric is a full service electrical contracting shop. We offer commercial, residential, light industrial, and agricultural services.</p>
  <p class="abs" style="left:79px;top:1792px;width:560px;font-size:14px;line-height:30px;color:var(--body)">M&amp;T Electric is a full service electrical contracting shop. We offer commercial, residential, light industrial, and agricultural services. We're Velmora Housepilot and Velmora Motorized Shades certified, as well as an authorized Brightvolt generator dealer. We've served the Alder Valley and Upper Plains area for over 18 years.</p>
  <span class="abs btn" style="left:79px;top:1914px">Know More</span>
  <div class="abs" style="left:670px;top:1652px;width:452px;height:316px;border-top:3px solid #111;border-right:3px solid #111"></div>
  <div class="abs" style="left:668px;top:1654px;width:438px;height:314px;border-left:3px solid #111;border-bottom:3px solid #111"></div>
  <div class="abs" role="img" aria-label="Single-storey company office building" style="left:690px;top:1673px;width:412px;height:278px;background:linear-gradient(#8c97a8,#a39b8e 55%,#6d6a66)"></div>
</section>

<div class="abs gal-band"></div>
<div class="abs gal-head"></div>
<h2 class="abs section-title" style="top:2064px;font-size:48px">Our Gallery</h2>
<div class="abs tabs"><span class="on">All</span><span>Commercial</span><span>Residential</span><span>Landscape</span></div>

<div class="abs tile" style="left:79px;top:2240px" role="img" aria-label="Commercial building at dusk"><div style="width:100%;height:100%;background:linear-gradient(#4c6aa8,#b9c0cc 60%,#556)"></div><div class="cap">M&amp;T Electric</div></div>
<div class="abs tile" style="left:439px;top:2240px" role="img" aria-label="Lit residence at twilight"><div style="width:100%;height:100%;background:linear-gradient(#3b4a80,#8a6f5a 60%,#4a4038)"></div><div class="cap">M&amp;T Electric</div></div>
<div class="abs tile" style="left:798px;top:2240px" role="img" aria-label="Illuminated home exterior"><div style="width:100%;height:100%;background:linear-gradient(#4d5a88,#b0805a 60%,#5a4a3c)"></div><div class="cap">M&amp;T Electric</div></div>
<div class="abs tile" style="left:79px;top:2492px" role="img" aria-label="Mountain home at dusk"><div style="width:100%;height:100%;background:linear-gradient(#8f86b0,#d3ccd8 55%,#6f6a7a)"></div><div class="cap">M&amp;T Electric</div></div>
<div class="abs tile" style="left:439px;top:2492px" role="img" aria-label="Modern interior with lighting"><div style="width:100%;height:100%;background:linear-gradient(#3a3a3a,#9a9590 55%,#6a6560)"></div><div class="cap">M&amp;T Electric</div></div>
<div class="abs tile" style="left:798px;top:2492px" role="img" aria-label="Commercial storefront at dusk"><div style="width:100%;height:100%;background:linear-gradient(#5d74b0,#a8866a 55%,#4a3e36)"></div><div class="cap">M&amp;T Electric</div></div>
<span class="abs btn ghost" style="left:506px;top:2733px">View More</span>

<h2 class="abs section-title" style="top:2912px;font-size:48px">Our Product</h2>
<div class="abs prod" style="left:62px">
  <div class="ph" role="img" aria-label="Wall keypad control" style="width:110px;background:linear-gradient(#444,#111)"></div>
  <h4>Velmora Housepilot</h4>
  <p>We're proudly certified to install Velmora Housepilot systems. It gives you complete</p>
</div>
<div class="abs prod" style="left:333px">
  <div class="ph" role="img" aria-label="Motorized shade brochure" style="width:150px;background:linear-gradient(#f3f3f3,#cfcfcf)"></div>
  <h4>Velmora Shadeline<br>Motorized Shades</h4>
  <p>Velmora Motorized Shades allow you to automatically adjust the natural lighting in your home.</p>
</div>
<div class="abs prod active" style="left:601px">
  <div class="ph" role="img" aria-label="Assorted LED light bulbs" style="width:200px;background:linear-gradient(#fafafa,#d4d4d4)"></div>
  <h4>LED Lighting</h4>
  <p>LED Lighting has rapidly become a functional and affordable option. LED Lighting is a high.</p>
</div>
<div class="abs prod" style="left:872px">
  <div class="ph" role="img" aria-label="Standby power generator unit" style="width:190px;background:linear-gradient(#eee,#b8b8b8)"></div>
  <h4>Emergency Generators</h4>
  <p>Never be without power again - protect yourself from frozen pipes, inconvenience, spoiled food.</p>
</div>

<section class="abs news">
  <h2 class="abs">Newsletter</h2>
  <div class="abs field">Enter Email*</div>
  <svg class="abs" style="left:828px;top:80px" width="20" height="15" viewBox="0 0 24 18"><rect x="1" y="1" width="22" height="16" fill="none" stroke="#333" stroke-width="2"/><path d="M1 1l11 9 11-9" fill="none" stroke="#333" stroke-width="2"/></svg>
  <span class="abs btn">Subscribe</span>
</section>

<footer class="abs footer">
  <div class="abs flogo wordmark">M&amp;T Electric</div>
  <div class="abs fsocial"><span></span><span></span><span></span></div>
  <div class="abs fcol" style="left:344px">
    <h5>SITEMAP</h5>
    <div>› Home</div><div>› About</div><div>› Speciality Services</div><div>› Product</div><div>› Gallery</div><div>› Contact</div>
  </div>
  <div class="abs fcol" style="left:608px">
    <h5>SERVICES</h5>
    <div>› Velmora Housepilot</div><div>› Velmora Shadeline Motorized Shades</div><div>› LED Lighting</div><div>› Emergency Generators</div>
  </div>
  <div class="abs fcol" style="left:872px">
    <h5>CONTACT US</h5>
    <div class="crow"><svg width="18" height="24" viewBox="0 0 18 24" style="margin-top:4px"><path d="M9 1a8 8 0 0 0-8 8c0 6 8 14 8 14s8-8 8-14a8 8 0 0 0-8-8z" fill="none" stroke="#ccc" stroke-width="2"/><circle cx="9" cy="9" r="3" fill="#ccc"/></svg><div><b style="color:#fff;font-weight:600">M&amp;T Electric</b><br>220 Quarry Lane PO Box 410<br>Harlow Bend, ST 00410</div></div>
    <div class="crow"><svg width="18" height="18" viewBox="0 0 24 24" style="margin-top:6px"><path fill="#ccc" d="M6.6 10.8a15 15 0 0 0 6.6 6.6l2.2-2.2c.3-.3.7-.4 1-.2 1.1.4 2.3.6 3.6.6.6 0 1 .4 1 1V20c0 .6-.4 1-1 1A17 17 0 0 1 3 4c0-.6.4-1 1-1h3.5c.6 0 1 .4 1 1 0 1.3.2 2.5.6 3.6.1.3 0 .7-.2 1z"/></svg><div>(555) 014-2290</div></div>
    <div class="crow"><svg width="18" height="14" viewBox="0 0 24 18" style="margin-top:8px"><rect x="1" y="1" width="22" height="16" fill="none" stroke="#ccc" stroke-width="2"/><path d="M1 1l11 9 11-9" fill="none" stroke="#ccc" stroke-width="2"/></svg><div>office@mandtelectric.example</div></div>
    <div class="crow"><svg width="18" height="14" viewBox="0 0 24 18" style="margin-top:8px"><rect x="1" y="1" width="22" height="16" fill="none" stroke="#ccc" stroke-width="2"/><path d="M1 1l11 9 11-9" fill="none" stroke="#ccc" stroke-width="2"/></svg><div>sales@mandtelectric.example</div></div>
  </div>
</footer>
<div class="abs copy">©M&amp;T Electric- 2017. All rights reserved.</div>

</body>
</html>
```